All-Natural Head Lice Removal company

I need a business card with my pre-existing logo. We are a new company located in Portland Oregon that goes into peoples homes to help with head lice removal. My products and approach are all- natural and also will be around children.On my current logo we used Teal Bl and the color Green. I am open to new ideas just want it simple and creative

Target Market(s)

my biggest market is families of school aged children

Industry/Entity Type

Business

Contact Information for Business Card

see upload for details from previous business card

Font styles to use
Serif

Colors
33a6d7
9bcb3b
f37122

Requirements
Must have
• Basic information/ logo put into a creative format that is catching to the eye
Nice to have
• creative

```html
<!DOCTYPE html>
<html lang="en">
<head>
<meta charset="utf-8">
<title>NitWise Business Card</title>
<link rel="stylesheet" href="https://fonts.googleapis.com/css2?family=Comic+Neue:wght@400;700&display=swap">
<style>
  :root {
    --page-bg: #e9e6e1;
    --card-frost: #eceeed;
    --green-deep: #3f9a1c;
    --green-bright: #6cc33a;
    --green-soft: rgba(120, 200, 70, 0);
    --text-light: #f3f8ea;
    --text-accent: #ffffff;
    --brand-green: #4f9e2a;
    --brand-ink: #1d1d1d;
    --lens-blue: #33a6d7;
  }
  * { margin: 0; padding: 0; box-sizing: border-box; }
  html, body {
    width: 1200px;
    height: 969px;
    overflow: hidden;
    background: var(--page-bg);
  }
  .business-card {
    position: absolute;
    left: 100px;
    top: 200px;
    width: 1000px;
    height: 568px;
    border-radius: 34px;
    overflow: hidden;
    background: var(--card-frost);
    box-shadow: 0 10px 30px rgba(0, 0, 0, 0.18);
    font-family: "Comic Neue", "Comic Sans MS", sans-serif;
  }
  .green-field {
    position: absolute;
    inset: 0;
    background: linear-gradient(90deg, var(--green-deep) 0%, var(--green-bright) 45%, rgba(108, 195, 58, 0.85) 58%, var(--green-soft) 78%);
  }
  .magnifier-art {
    position: absolute;
    left: 405px;
    top: 0;
    width: 255px;
    height: 568px;
    border-radius: 0 0 40px 40px;
    background: linear-gradient(180deg, rgba(51, 166, 215, 0.85) 0%, rgba(63, 150, 60, 0.9) 55%, rgba(30, 40, 30, 0.55) 100%);
  }
  .owner-block {
    position: absolute;
    left: 52px;
    top: 58px;
    color: var(--text-light);
  }
  .owner-name {
    font-size: 36px;
    font-weight: 700;
    letter-spacing: 0.5px;
  }
  .owner-title {
    font-size: 27px;
    margin-top: 2px;
  }
  .tagline {
    position: absolute;
    left: 52px;
    top: 248px;
    font-size: 27px;
    line-height: 35px;
    color: var(--text-light);
  }
  .tagline strong { color: var(--text-accent); font-weight: 700; }
  .contact-list {
    position: absolute;
    left: 52px;
    top: 408px;
    list-style: none;
    font-size: 26px;
    line-height: 40px;
    color: var(--text-light);
  }
  .contact-list li { display: flex; align-items: center; gap: 12px; }
  .contact-list li.phone { font-size: 28px; }
  .contact-icon { width: 24px; height: 24px; fill: var(--text-light); flex: none; }
  .brand-mark {
    position: absolute;
    left: 700px;
    top: 320px;
    display: flex;
    align-items: center;
    gap: 14px;
  }
  .brand-dot {
    width: 64px;
    height: 64px;
    border-radius: 50%;
    background: var(--brand-green);
  }
  .brand-name {
    font-size: 58px;
    font-weight: 700;
    color: var(--brand-ink);
  }
</style>
</head>
<body>
  <div class="business-card">
    <div class="green-field"></div>
    <div class="magnifier-art" role="img" aria-label="Illustration of a large magnifying glass with a cartoon eye inside the lens"></div>

    <div class="owner-block">
      <div class="owner-name">Marla Quinlan</div>
      <div class="owner-title">Owner</div>
    </div>

    <p class="tagline">
      Try NitWise Today &amp;<br>
      Be Lice Free Tomorrow!<br>
      <strong>All Natural In-Home<br>
      Lice Removal Services</strong>
    </p>

    <ul class="contact-list">
      <li class="phone">
        <svg class="contact-icon" viewBox="0 0 24 24" aria-hidden="true"><path d="M6.6 10.8a15.1 15.1 0 0 0 6.6 6.6l2.2-2.2a1 1 0 0 1 1-.25 11.4 11.4 0 0 0 3.6.57 1 1 0 0 1 1 1V20a1 1 0 0 1-1 1A17 17 0 0 1 3 4a1 1 0 0 1 1-1h3.5a1 1 0 0 1 1 1c0 1.25.2 2.45.57 3.57a1 1 0 0 1-.25 1z"/></svg>
        1-855-555-0142
      </li>
      <li>
        <svg class="contact-icon" viewBox="0 0 24 24" aria-hidden="true"><path d="M3 5h18v14H3z M3 5l9 7 9-7" fill="none" stroke="#f3f8ea" stroke-width="2"/></svg>
        marla@nitwise.com
      </li>
      <li>
        <svg class="contact-icon" viewBox="0 0 24 24" aria-hidden="true"><circle cx="12" cy="12" r="9" fill="none" stroke="#f3f8ea" stroke-width="2"/><path d="M3 12h18M12 3c3 3 3 15 0 18M12 3c-3 3-3 15 0 18" fill="none" stroke="#f3f8ea" stroke-width="1.6"/></svg>
        www.nitwise.com
      </li>
    </ul>

    <div class="brand-mark">
      <span class="brand-dot"></span>
      <span class="brand-name">NitWise</span>
    </div>
  </div>
</body>
</html>
```